professional business card design

Business card design. Photos have been uploaded and i am open to the designer choosing which photos to use. Would like the card to be mostyly in a grey scale design with black, whites, silver & grey colours. I have added copy of our flyer as would like on the back side of card our services to be listed. Do not use any bright colurs such as blue red green or yellow. i need to be able to edit the phone number and naem in the final card design submitted.

Target Market(s)

Clients

Industry/Entity Type

earhmovibng and transport

Contact Information for Business Card

Director Name, address, email, phone number and services

Colors

Designer to choose only greyscale colors for use in the design.

Requirements
Should not have
• no yellow, red, blue or green

```html
<!DOCTYPE html>
<html lang="en">
<head>
<meta charset="utf-8">
<title>RPH Pty Ltd – Business Card</title>
<link rel="stylesheet" href="https://fonts.googleapis.com/css2?family=Russo+One&family=Open+Sans:wght@400;600&display=swap">
<style>
  :root {
    --page: #d8d5d1;
    --ink: #0d0d0d;
    --card-black: #121110;
    --white: #ffffff;
    --silver-light: #f4f4f4;
    --silver-mid: #bdbdbd;
    --silver-dark: #8e8e8e;
    --steel: #2b2b2b;
    --earth-1: #7a4a2a;
    --earth-2: #b77b4d;
    --logo-grey: #c9c9c9;
  }
  * { box-sizing: border-box; margin: 0; padding: 0; }
  html, body { width: 900px; height: 1200px; overflow: hidden; }
  body {
    background: var(--page);
    font-family: "Open Sans", Arial, sans-serif;
    position: relative;
  }
  .card {
    position: absolute;
    left: 78px;
    width: 744px;
    height: 444px;
    border-radius: 26px;
    overflow: hidden;
    background: var(--card-black);
    box-shadow: 0 6px 14px rgba(0,0,0,.35);
  }
  .card--front { top: 130px; }
  .card--back { top: 638px; }

  .silver-band {
    position: absolute;
    left: 0; right: 0;
    background: linear-gradient(90deg, var(--white) 0%, var(--silver-light) 25%, var(--silver-mid) 55%, var(--white) 75%, var(--silver-dark) 100%);
    display: flex; align-items: center; justify-content: center;
    font-family: "Russo One", Arial, sans-serif;
    color: var(--ink);
  }

  /* front */
  .hero-photo {
    position: absolute; left: 0; top: 0; width: 744px; height: 266px;
    background:
      linear-gradient(180deg, #050505 0%, #1c1c1c 40%, #3a2f27 62%, var(--earth-1) 80%, var(--earth-2) 100%);
  }
  .brand-mark {
    position: absolute;
    font-family: "Russo One", Arial, sans-serif;
    color: var(--logo-grey);
    letter-spacing: 4px;
    text-align: center;
    left: 0; right: 0;
  }
  .card--front .brand-mark { top: 28px; font-size: 70px; line-height: 1; }
  .company-band { top: 266px; height: 34px; font-size: 25px; letter-spacing: 1px; }
  .contact-panel {
    position: absolute; top: 300px; left: 0; right: 0; height: 108px;
    background: var(--card-black); color: var(--white);
  }
  .person { position: absolute; right: 414px; top: 30px; text-align: right; }
  .person__name { font-family: "Russo One", Arial, sans-serif; font-size: 25px; line-height: 1; letter-spacing: .5px; }
  .person__role { font-family: "Russo One", Arial, sans-serif; font-size: 15px; margin-top: 4px; }
  .divider { position: absolute; left: 355px; top: 24px; width: 2px; height: 64px; background: #bdbdbd; }
  .contact-list { position: absolute; left: 378px; top: 20px; list-style: none; }
  .contact-list li {
    display: flex; align-items: center; gap: 16px;
    font-family: "Russo One", Arial, sans-serif;
    font-size: 15.5px; height: 23px; letter-spacing: .3px;
  }
  .contact-list svg { width: 14px; height: 14px; fill: #9a9a9a; flex: none; }
  .depot-band { top: 408px; height: 36px; font-size: 16px; letter-spacing: .3px; }

  /* back */
  .steel-panel {
    position: absolute; left: 0; top: 0; width: 744px; height: 274px;
    background: radial-gradient(ellipse at 50% 40%, #4a4a4a 0%, #2a2a2a 55%, #121212 100%);
  }
  .card--back .brand-mark { top: 60px; font-size: 118px; line-height: 1; }
  .card--back .brand-sub {
    position: absolute; top: 212px; left: 0; right: 0; text-align: center;
    font-family: "Russo One", Arial, sans-serif; font-size: 30px; color: #9b9b9b;
  }
  .services-band { top: 274px; height: 45px; font-size: 23px; }
  .services {
    position: absolute; top: 330px; left: 20px; right: 20px;
    color: var(--white); font-size: 14.5px; text-align: center; line-height: 26.5px;
  }
  .services span { white-space: nowrap; }
  .services .sep { margin: 0 12px; }
</style>
</head>
<body>

<section class="card card--front" aria-label="Business card front">
  <div class="hero-photo" role="img" aria-label="Photo of a road train truck hauling three tipper trailers on a red outback dirt road"></div>
  <div class="brand-mark">RPH</div>
  <div class="silver-band company-band">RPH PTY LTD</div>
  <div class="contact-panel">
    <div class="person">
      <p class="person__name">DANIEL CORWIN</p>
      <p class="person__role">Director</p>
    </div>
    <div class="divider"></div>
    <ul class="contact-list">
      <li><svg viewBox="0 0 16 16" aria-hidden="true"><path d="M2 5c0-2 2-3 6-3s6 1 6 3v1h-3V5H5v1H2zM4 7h8l2 6H2z"/></svg>000 555 000</li>
      <li><svg viewBox="0 0 16 16" aria-hidden="true"><path d="M1 3h14v10H1z M2 4l6 5 6-5" stroke="#121110" stroke-width="1"/></svg>info@redplainhaulage.com.au</li>
      <li><svg viewBox="0 0 16 16" aria-hidden="true"><circle cx="8" cy="8" r="7"/><path d="M4 5h4v3H5z M9 9h3v3H9z" fill="#121110"/></svg>www.redplainhaulage.com.au</li>
    </ul>
  </div>
  <div class="silver-band depot-band">DEPOT :RPH LOT 114, QUARRY FLAT ROAD, DUNMORE RIDGE, AUSTRALIA</div>
</section>

<section class="card card--back" aria-label="Business card back">
  <div class="steel-panel" role="img" aria-label="Dark perforated steel texture"></div>
  <div class="brand-mark">RPH</div>
  <div class="brand-sub">Pty Ltd</div>
  <div class="silver-band services-band">OUR SERVICES</div>
  <p class="services">
    <span>Mine site accredited equipment &amp; oparetors</span><span class="sep">|</span><span>Drop Deck Trailers</span><span class="sep">|</span><span>Road train flat tops</span><br>
    <span>Road train Tankers</span><span class="sep">|</span><span>Road train Trippers</span><span class="sep">|</span><span>Send &amp; Metal Supply &amp; cartage</span><span class="sep">|</span><span>Earthworks</span><br>
    <span>Road Building / Maintenance</span><span class="sep">|</span><span>potable water delivers</span><span class="sep">|</span><span>Heavy Vehicle Recovery services</span><br>
    <span>Over size load / Hot Shot Load</span>
  </p>
</section>

</body>
</html>
```